Doctor to Patient Management Website

I need a design for a health management website that connects doctors to patients. The website will consist of: A main page mainly describing our goal, services, and initiatives towards (Who we are AKA "About Us", Our services, Contact Us, Quick Links for health tips, Language selection, Find a doctor, search bar, Member Login Section, small glossary section below with links to all entities mentioned prior, Help section (Helpful tips and tutorials, Used to request help from admin, customer service, to resolve issues or get assistance). A profile page with two types:1) Doctor Profile: Doctor Personal info (First, Last, Middle Name, Title), Clinic, Hospital Info, Department, Credentials, Years of Experience, Patients rating, #Patients seen during the current week, #Patients seen in total, Picture, Link to email doctor, Link to print doctor's profile). Tabs for "About Me", "Contact Info", "Ratings & Comments", "Documents" (To be downloaded and uploaded by patient), "Patients (List of Patients alphabetical order by name)", "Calendar" (to see doctor's availability for booking) underneath all links. 2) Patient profile: About me, Personal Info, Height, Weight, Blood Type, Age, DOB, Name, etc..., Message and email link.Picture of patient with menu made of "Personal Data", "Biometrics", "Allergies", "Illnesses", "Medications", "Medical Procedures", "Doctors" treating the patient, "Documents" (To be downloaded and uploaded by patient). Underneath all, other patients he or she is related to (For example: family member, so patient can't connect to other patients who are family members)3) Login section: New Users will have option to register using:First Name (Required), Last Name, Middle (not required), Address (Not required), City (Required), Country (Required), Email (Not required), Phone Number (Required), Choose UserName, Password, Account Type (Doctor or Patient). Once registered, they will log in using UserName, Password, and Account_Type.Curent Users will log in using UserName, Password, and Account_Type and option to retrieve username or password.Pages to include (Login Page - Registration Page - Retrieve Username and Reset Password Page)Please see link below:https://plumcrate-adwerks.net/importance-claiming-vantorix-quibble-zarn/Pictures are attached to this project as an inspirationFYI: Dummy text can be used to fill in the business, services, and descriptive information. Feel free to include your own ideas in the layout, design, categories, patterns, and more to and showcase your talent. Design and pictures provided are available as source of ideas.

Target Market(s)

Age: 21+ / Family Oriented / Medical Sector / Metropolitan Area / Educated and non Educated Users

Industry/Entity Type

Health Care

Number of Pages Required

5+ page

Font styles to use
Sans Serif

Colors

Designer to choose colors to be used in the design.

Requirements
Must have
• Thin layer design
• Simple font - No serif
• Clean menu with light but solid colors (No Gradient effect)
Nice to have
• Different color themes (2 or 3) can be combined
• Sample pictures for illustration (either as an ad or to go with the flow of your design)
• Dashboard Feel (Suggested but not required)
Should not have
• Artistic fonts - with Serif
• Dark color themes

```html
<!DOCTYPE html>
<html lang="en">
<head>
<meta charset="utf-8">
<title>Halvora – Doctor to Patient Care</title>
<link href="https://fonts.googleapis.com/css2?family=Poppins:wght@400;500;600;700&display=swap" rel="stylesheet">
<style>
:root{
  --blue:#1e9bd7;
  --green:#4cb848;
  --dark:#222;
  --text:#555;
  --muted:#888;
  --grey-bg:#f0f0f0;
  --footer:#0b0b0b;
  --white:#fff;
  --teal:#2a8fb8;
}
*{box-sizing:border-box;margin:0;padding:0}
html,body{width:1200px;height:5000px;overflow:hidden}
body{font-family:'Poppins',sans-serif;color:var(--text);background:var(--white);position:relative}
.abs{position:absolute}
.topbar{left:0;top:0;width:1200px;height:40px;background:var(--blue);color:#fff;font-size:13px;display:flex;align-items:center;justify-content:space-between;padding:0 90px}
.topbar .contact{display:flex;gap:28px;align-items:center}
.topbar .contact span{display:flex;gap:6px;align-items:center}
.topbar .right{display:flex;gap:14px;align-items:center}
.btn-login{background:var(--green);color:#fff;font-size:11px;padding:4px 12px;border-radius:3px}
.dot{width:12px;height:12px;border-radius:50%;background:rgba(255,255,255,.85)}
.nav{left:0;top:40px;width:1200px;height:100px;display:flex;align-items:center;justify-content:space-between;padding:0 90px;background:#fff}
.brand{display:flex;align-items:center;gap:12px;font-size:34px;font-weight:600;color:var(--dark)}
.brand .mark{width:40px;height:40px;border-radius:50%;background:var(--green)}
.menu{display:flex;gap:26px;font-size:15px;font-weight:500;color:var(--dark)}
.menu .active{color:var(--green)}
.hero-photo{left:0;top:140px;width:1200px;height:700px;background:linear-gradient(90deg,#3a3f44 0%,#6f7a80 55%,#b9c2c6 100%)}
.hero-shade{left:0;top:140px;width:1200px;height:700px;background:rgba(0,0,0,.25)}
.hero-title{left:90px;top:360px;font-size:46px;font-weight:700;color:#fff}
.hero-copy{left:90px;top:430px;width:460px;font-size:19px;line-height:1.5;color:#fff}
.search{left:90px;top:550px;width:440px;height:54px;background:#fff;border-radius:3px;display:flex;align-items:center;justify-content:space-between;padding:0 8px 0 18px;font-size:16px;color:var(--dark)}
.search .go{background:var(--green);color:#fff;font-size:15px;padding:8px 34px;border-radius:3px}
.badge{left:540px;top:775px;width:120px;height:120px;border-radius:50%;background:#fff;box-shadow:0 4px 14px rgba(0,0,0,.15);display:flex;align-items:center;justify-content:center}
.badge span{width:58px;height:58px;border-radius:50%;background:var(--green)}
h2.title{width:1200px;left:0;text-align:center;font-size:40px;font-weight:600;color:var(--dark)}
.lead{left:240px;width:720px;text-align:center;font-size:15px;line-height:1.9;color:var(--muted)}
.wwd-img{left:0;top:1240px;width:810px;height:480px;background:linear-gradient(135deg,#cfd6da,#e9ecef 60%,#aab3b8)}
.wwd-card{left:670px;top:1280px;width:530px;height:380px;background:#fff;box-shadow:0 4px 20px rgba(0,0,0,.15);padding:50px 56px}
.wwd-card h3{font-size:34px;font-weight:600;color:var(--dark);margin-bottom:20px}
.wwd-card p{font-size:15px;line-height:1.85;color:var(--muted);margin-bottom:28px}
.btn{display:inline-block;background:var(--green);color:#fff;font-size:15px;font-weight:500;padding:12px 38px;border-radius:30px}
.service{top:1920px;width:330px;height:480px;background:#fff;box-shadow:0 2px 12px rgba(0,0,0,.15);text-align:center}
.service .ph{height:200px;background:linear-gradient(135deg,#d8dee2,#9aa8b0)}
.service .ico{width:66px;height:66px;border-radius:50%;background:var(--blue);border:5px solid #fff;margin:-36px auto 0;position:relative;display:flex;align-items:center;justify-content:center}
.service h4{font-size:20px;font-weight:600;color:var(--dark);margin:12px 0 10px}
.service p{font-size:14px;line-height:1.7;padding:0 30px;color:var(--text);margin-bottom:30px}
.service .btn{font-size:14px;padding:9px 42px}
.team-band{left:0;top:2500px;width:1200px;height:630px;background:var(--grey-bg)}
.member{top:2750px;width:200px;text-align:center}
.member .ph{width:170px;height:170px;margin:0 auto;border-radius:50%;background:linear-gradient(160deg,#e3e7ea,#a9b5bc);border:4px solid #fff}
.member .social{width:170px;height:40px;margin:-30px auto 0;position:relative;background:var(--green);border-radius:20px;display:flex;justify-content:center;align-items:center;gap:14px}
.member .social i{width:13px;height:13px;border-radius:50%;background:#fff;display:block}
.member h5{margin-top:40px;font-size:18px;font-weight:600;color:var(--dark)}
.tips-title{color:var(--teal)!important}
.tip-big{left:90px;top:3320px;width:500px;height:340px;background:#fff;box-shadow:0 2px 12px rgba(0,0,0,.15);display:flex}
.tip-big .ph{width:250px;background:linear-gradient(135deg,#c98a4b,#e8d4b5 55%,#8fa86a)}
.tip-body{padding:30px 22px;font-size:15px;line-height:1.7;color:var(--dark)}
.tip-body p+p{margin-top:14px;color:var(--text)}
.link{color:var(--green);font-size:14px;margin-top:16px;display:block}
.tip-small{left:600px;width:510px;height:160px;background:#fff;box-shadow:0 2px 12px rgba(0,0,0,.15);display:flex}
.tip-small .body{flex:1;padding:18px 22px;font-size:14px;line-height:1.55;color:var(--dark)}
.tip-small .body .sub{font-size:13px;color:var(--text);margin-top:8px}
.tip-small .body .link{margin-top:8px}
.tip-small .ph{width:200px;background:linear-gradient(135deg,#5c3a2a,#c4a07c)}
.tip-small .ph.alt{background:linear-gradient(135deg,#e7e2da,#b9c9a3)}
.testi-band{left:0;top:3770px;width:1200px;height:620px;background:var(--grey-bg)}
.testi{top:3980px;width:320px;text-align:center}
.testi .avatar{width:86px;height:86px;border-radius:50%;margin:0 auto -40px;position:relative;z-index:2;background:linear-gradient(160deg,#c9a88e,#6c5143);border:4px solid #fff}
.testi .bubble{background:#fff;box-shadow:0 2px 12px rgba(0,0,0,.12);border-radius:6px;padding:56px 30px 30px;font-size:13px;line-height:1.7;color:var(--muted);position:relative;z-index:1}
.testi .bubble:after{content:"";position:absolute;left:150px;bottom:-12px;border:12px solid transparent;border-bottom:0;border-top-color:#fff}
.testi .who{margin-top:26px;font-size:17px;color:var(--teal);line-height:1.4}
.testi .stars{margin-top:8px;color:#f5a623;font-size:18px;letter-spacing:2px}
.footer{left:0;top:4420px;width:1200px;height:580px;background:var(--footer)}
.fcol{top:4500px;color:#fff}
.fcol h6{font-size:20px;font-weight:600;margin-bottom:22px;color:#fff}
.fcol li{list-style:none;font-size:14px;line-height:2;color:#ddd}
.fitem{display:flex;gap:14px;font-size:14px;line-height:1.6;color:#ddd;margin-bottom:18px}
.fitem .ic{width:26px;height:26px;border-radius:50%;border:1px solid #fff;flex:none;display:flex;align-items:center;justify-content:center}
.fsocial{left:0;top:4880px;width:1200px;display:flex;justify-content:center;gap:14px}
.fsocial i{width:34px;height:34px;border-radius:50%;border:1px solid #fff;display:block}
.copy{left:0;top:4940px;width:1200px;text-align:center;font-size:13px;color:#ccc}
</style>
</head>
<body>

<div class="abs topbar">
  <div class="contact">
    <span><svg width="12" height="12" viewBox="0 0 24 24"><path fill="#fff" d="M6.6 10.8a15 15 0 006.6 6.6l2.2-2.2c.3-.3.7-.4 1-.2 1.1.4 2.3.6 3.6.6.6 0 1 .4 1 1V20c0 .6-.4 1-1 1A17 17 0 013 4c0-.6.4-1 1-1h3.5c.6 0 1 .4 1 1 0 1.3.2 2.5.6 3.6.1.3 0 .7-.2 1z"/></svg>800-214-7730</span>
    <span><svg width="13" height="10" viewBox="0 0 26 20"><rect x="1" y="1" width="24" height="18" fill="none" stroke="#fff" stroke-width="2"/><path d="M1 1l12 10L25 1" fill="none" stroke="#fff" stroke-width="2"/></svg>hello@halvora-care.net</span>
  </div>
  <div class="right">
    <span class="btn-login">Member Login</span>
    <i class="dot"></i><i class="dot"></i><i class="dot"></i><i class="dot"></i>
  </div>
</div>

<header class="abs nav">
  <div class="brand"><span class="mark"></span>Halvora</div>
  <nav class="menu">
    <span class="active">Home</span><span>About Us</span><span>Our Services</span><span>Our Goal</span><span>Help</span><span>Contact Us</span>
  </nav>
</header>

<section>
  <div class="abs hero-photo" role="img" aria-label="Photo of doctors consulting together in a bright clinic office"></div>
  <div class="abs hero-shade"></div>
  <h1 class="abs hero-title">Welcome to Halvora</h1>
  <p class="abs hero-copy">Lorem ipsum dolor sit amet, consectetur adipiscing elit, sed do eiusmod tempor incididunt ut labore et dolore magna aliqua Ut enim ad minim.</p>
  <div class="abs search"><span>Find a doctor</span><span class="go">Search</span></div>
  <div class="abs badge"><span></span></div>
</section>

<section>
  <h2 class="abs title" style="top:1000px">About Us</h2>
  <p class="abs lead" style="top:1066px">Lorem Ipsum is simply dummy text of the printing and typesetting industry. Lorem Ipsum has been the industry's standard dummy text ever since the 1500s, when an unknown printer took a galley of type and scrambled it to make a type specimen book.</p>
  <div class="abs wwd-img" role="img" aria-label="Photo of a medical team meeting around a table"></div>
  <div class="abs wwd-card">
    <h3>What We Do</h3>
    <p>Lorem Ipsum is simply dummy text of the printing and typesetting industry. Lorem Ipsum has been the industry's standard dummy text ever since the 1500s, when an unknown printer took a galley of type.</p>
    <span class="btn">Read More</span>
  </div>
</section>

<section>
  <h2 class="abs title" style="top:1810px">Services</h2>
  <div class="abs service" style="left:90px">
    <div class="ph" role="img" aria-label="Photo of hospital staff greeting a visitor"></div>
    <div class="ico"><svg width="26" height="26" viewBox="0 0 24 24"><path fill="#fff" d="M10 3h4v7h7v4h-7v7h-4v-7H3v-4h7z"/></svg></div>
    <h4>Hospitality</h4>
    <p>Lorem Ipsum is simply dummy text of the printing and typesetting industry. Lorem Ipsum has been the industry's</p>
    <span class="btn">Read More</span>
  </div>
  <div class="abs service" style="left:435px">
    <div class="ph" role="img" aria-label="Photo of a doctor writing notes at a desk"></div>
    <div class="ico"><svg width="26" height="26" viewBox="0 0 24 24"><path fill="#fff" d="M10 3h4v7h7v4h-7v7h-4v-7H3v-4h7z"/></svg></div>
    <h4>Medical Service</h4>
    <p>Lorem Ipsum is simply dummy text of the printing and typesetting industry. Lorem Ipsum has been the industry's</p>
    <span class="btn">Read More</span>
  </div>
  <div class="abs service" style="left:780px">
    <div class="ph" role="img" aria-label="Photo of a lab worker handling vaccine vials"></div>
    <div class="ico"><svg width="26" height="26" viewBox="0 0 24 24"><path fill="none" stroke="#fff" stroke-width="2.4" d="M4 20l6-6M8 12l4 4M9 9l6 6 6-6-6-6z"/></svg></div>
    <h4>Vaccines</h4>
    <p>Lorem Ipsum is simply dummy text of the printing and typesetting industry. Lorem Ipsum has been the industry's</p>
    <span class="btn">Read More</span>
  </div>
</section>

<section>
  <div class="abs team-band"></div>
  <h2 class="abs title" style="top:2590px">Our Team</h2>
  <div class="abs member" style="left:95px"><div class="ph" role="img" aria-label="Portrait of a team doctor"></div><div class="social"><i></i><i></i><i></i><i></i></div><h5>Dr. Lorcan</h5></div>
  <div class="abs member" style="left:365px"><div class="ph" role="img" aria-label="Portrait of a team doctor"></div><div class="social"><i></i><i></i><i></i><i></i></div><h5>Dr. Maren Holt</h5></div>
  <div class="abs member" style="left:630px"><div class="ph" role="img" aria-label="Portrait of a team doctor"></div><div class="social"><i></i><i></i><i></i><i></i></div><h5>Dr. Tobias Renn</h5></div>
  <div class="abs member" style="left:900px"><div class="ph" role="img" aria-label="Portrait of a team doctor"></div><div class="social"><i></i><i></i><i></i><i></i></div><h5>Dr. Selwyn</h5></div>
</section>

<section>
  <h2 class="abs title tips-title" style="top:3200px">Health Tips</h2>
  <div class="abs tip-big">
    <div class="ph" role="img" aria-label="Photo of healthy food and vitamin pills"></div>
    <div class="tip-body">
      <p>Lorem Ipsum is simply dummy text of the printing and typesetting industry Lorem</p>
      <p>It was popularised in the 1960s with the release of Letraset sheets containing Lorem</p>
      <span class="link">Read More</span>
    </div>
  </div>
  <div class="abs tip-small" style="top:3320px">
    <div class="body">qui dolorem ipsum quia dolor sit amet<div class="sub">It was popularised in the 1960s with the release of</div><span class="link">Read More</span></div>
    <div class="ph" role="img" aria-label="Photo of a plated meal"></div>
  </div>
  <div class="abs tip-small" style="top:3500px">
    <div class="ph alt" role="img" aria-label="Photo of a light breakfast table"></div>
    <div class="body">qui dolorem ipsum quia dolor sit amet<div class="sub">It was popularised in the 1960s with the release of</div><span class="link">Read More</span></div>
  </div>
</section>

<section>
  <div class="abs testi-band"></div>
  <h2 class="abs title" style="top:3860px">Patient Testimonials</h2>
  <div class="abs testi" style="left:95px"><div class="avatar" role="img" aria-label="Patient portrait"></div><div class="bubble">Sed ut perspiciatis unde omnis iste natus error sit voluptatem accusantium doloremque laudantium, totam rem aperiam, eaque ipsa.</div><div class="who">Idris Vale<br>USA</div><div class="stars">★★★★★</div></div>
  <div class="abs testi" style="left:440px"><div class="avatar" role="img" aria-label="Patient portrait"></div><div class="bubble">Sed ut perspiciatis unde omnis iste natus error sit voluptatem accusantium doloremque laudantium, totam rem aperiam, eaque ipsa.</div><div class="who">Idris Vale<br>USA</div><div class="stars">★★★★★</div></div>
  <div class="abs testi" style="left:785px"><div class="avatar" role="img" aria-label="Patient portrait"></div><div class="bubble">Sed ut perspiciatis unde omnis iste natus error sit voluptatem accusantium doloremque laudantium, totam rem aperiam, eaque ipsa.</div><div class="who">Idris Vale<br>USA</div><div class="stars">★★★★★</div></div>
</section>

<footer>
  <div class="abs footer"></div>
  <div class="abs fcol" style="left:95px">
    <h6>Quick Links</h6>
    <ul><li>Home</li><li>About Us</li><li>Our Services</li><li>Our Goal</li><li>Help section</li><li>Contact Us</li></ul>
  </div>
  <div class="abs fcol" style="left:380px;width:320px">
    <h6>Contact Us</h6>
    <div class="fitem"><span class="ic"><svg width="12" height="14" viewBox="0 0 24 28"><path fill="#fff" d="M12 0a10 10 0 00-10 10c0 8 10 18 10 18s10-10 10-18A10 10 0 0012 0zm0 14a4 4 0 110-8 4 4 0 010 8z"/></svg></span><span>Halvora Care<br>48 Harlow Lane<br>Suite 12 Crestview House<br>Brookfield 40211</span></div>
    <div class="fitem"><span class="ic"><svg width="12" height="12" viewBox="0 0 24 24"><path fill="#fff" d="M6.6 10.8a15 15 0 006.6 6.6l2.2-2.2c.3-.3.7-.4 1-.2 1.1.4 2.3.6 3.6.6.6 0 1 .4 1 1V20c0 .6-.4 1-1 1A17 17 0 013 4c0-.6.4-1 1-1h3.5c.6 0 1 .4 1 1 0 1.3.2 2.5.6 3.6.1.3 0 .7-.2 1z"/></svg></span><span>Call Us :<br>800 214 7730</span></div>
    <div class="fitem"><span class="ic"><svg width="12" height="12" viewBox="0 0 24 24"><circle cx="12" cy="12" r="10" fill="none" stroke="#fff" stroke-width="2"/><path d="M12 6v6l4 3" stroke="#fff" stroke-width="2" fill="none"/></svg></span><span>Mon – Fri (9.00PM – 9.00AM)<br>Sat – (9.00AM – 1PM)</span></div>
  </div>
  <div class="abs fcol" style="left:735px">
    <h6>Helpful Links</h6>
    <ul><li>Lorem Ipsum</li><li>Lorem Ipsum</li><li>Lorem Ipsum</li><li>Lorem Ipsum</li><li>Lorem Ipsum</li><li>Lorem Ipsum</li></ul>
  </div>
  <div class="abs fcol" style="left:995px">
    <h6>Glossary</h6>
    <ul><li>Lorem Ipsum</li><li>Lorem Ipsum</li><li>Lorem Ipsum</li><li>Lorem Ipsum</li><li>Lorem Ipsum</li><li>Lorem Ipsum</li></ul>
  </div>
  <div class="abs fsocial"><i></i><i></i><i></i></div>
  <p class="abs copy">Copyright 2018 | All rights reserved | Privacy Policy | Term &amp; Conditions</p>
</footer>

</body>
</html>
```